Carpet cleaning company focused on high quality needs business cards

We are a growing company that just merged with another company and need to design a new business card. We do both residential as well as commercial cleaning. We do carpet, tile & grout, upholstery, hard floors, and stain & pet odor removal. We treat our customers like family and strive to achieve outstanding results with every job.

```html
<!DOCTYPE html>
<html lang="en">
<head>
<meta charset="utf-8">
<title>Rowan's Fresh Floor Care – Business Card</title>
<link href="https://fonts.googleapis.com/css2?family=Montserrat:wght@400;500;800&display=swap" rel="stylesheet">
<style>
  :root {
    --backdrop: #26262a;
    --card-dark: #37373c;
    --card-light: #ffffff;
    --brand-red: #e8433a;
    --brand-red-soft: #f26a5f;
    --brand-blue: #2f86c6;
    --ink: #1d1d1f;
    --ink-soft: #333338;
    --white: #ffffff;
  }
  * { box-sizing: border-box; margin: 0; padding: 0; }
  html, body { width: 1200px; height: 900px; overflow: hidden; }
  body {
    background: var(--backdrop);
    font-family: "Montserrat", sans-serif;
    position: relative;
  }
  .card {
    position: absolute;
    left: 270px;
    width: 660px;
    height: 377px;
    border-radius: 26px;
    overflow: hidden;
    box-shadow: 0 16px 40px rgba(0,0,0,.45);
  }
  .card--back { top: 48px; background: var(--card-dark); }
  .card--front { top: 475px; background: var(--card-light); }

  /* back side */
  .back-logo {
    position: absolute;
    left: 120px; top: 92px;
    display: flex; align-items: center; gap: 22px;
  }
  .mascot-panel {
    width: 200px; height: 190px;
    background: linear-gradient(160deg, var(--brand-blue) 0%, var(--brand-red) 55%, var(--brand-red) 100%);
    clip-path: polygon(18% 0, 100% 0, 100% 100%, 0 100%);
  }
  .wordmark { font-weight: 800; line-height: .95; letter-spacing: -.5px; }
  .wordmark__main { font-size: 62px; display: block; }
  .wordmark__sub { font-size: 27px; display: block; letter-spacing: 0; }
  .card--back .wordmark { color: var(--white); }

  /* front side */
  .front-mascot {
    position: absolute;
    right: 0; top: 0;
    width: 330px; height: 377px;
    background: linear-gradient(200deg, var(--brand-blue) 0%, #5a8bb0 30%, var(--brand-red-soft) 62%, var(--brand-red) 100%);
    clip-path: polygon(35% 0, 100% 0, 100% 100%, 0 100%, 0 78%, 55% 35%);
  }
  .front-logo {
    position: absolute;
    left: 42px; top: 40px;
  }
  .card--front .wordmark { color: var(--ink); }
  .card--front .wordmark__main { font-size: 48px; }
  .card--front .wordmark__sub { font-size: 21px; }

  .contact {
    position: absolute;
    left: 42px; top: 168px;
    color: var(--ink-soft);
  }
  .contact__name {
    color: var(--brand-red);
    font-weight: 800;
    font-size: 28px;
    letter-spacing: -.3px;
  }
  .contact__role { font-size: 15px; margin-top: 2px; }
  .contact__address { font-size: 14px; line-height: 1.35; margin-top: 12px; }
  .contact__list { list-style: none; margin-top: 12px; }
  .contact__item {
    display: flex; align-items: center; gap: 10px;
    font-size: 14px; line-height: 1.55;
  }
  .contact__icon { width: 14px; height: 14px; flex: none; }
</style>
</head>
<body>

<section class="card card--back" aria-label="Business card, back">
  <div class="back-logo">
    <div class="mascot-panel" role="img" aria-label="Mascot illustration of a cleaner holding a steam wand on a red panel"></div>
    <div class="wordmark">
      <span class="wordmark__main">Rowan's</span>
      <span class="wordmark__sub">FRESH FLOOR</span>
      <span class="wordmark__sub">CARE</span>
    </div>
  </div>
</section>

<section class="card card--front" aria-label="Business card, front">
  <div class="front-mascot" role="img" aria-label="Mascot illustration of a cleaner spraying with a steam wand over a red corner panel"></div>

  <div class="front-logo wordmark">
    <span class="wordmark__main">Rowan's</span>
    <span class="wordmark__sub">FRESH FLOOR</span>
    <span class="wordmark__sub">CARE</span>
  </div>

  <div class="contact">
    <p class="contact__name">Daniel Porter</p>
    <p class="contact__role">CEO</p>
    <p class="contact__address">418 Maple Grove Ave, #112<br>Brookfield, OH 43190</p>
    <ul class="contact__list">
      <li class="contact__item">
        <svg class="contact__icon" viewBox="0 0 16 16" aria-hidden="true"><path fill="#e8433a" d="M2 5c0-2 2-3 6-3s6 1 6 3l-2 1-1-2H5L4 6 2 5zm2 2h8l1 7H3l1-7zm4 1.5a2 2 0 100 4 2 2 0 000-4z"/></svg>
        555 310-2746
      </li>
      <li class="contact__item">
        <svg class="contact__icon" viewBox="0 0 16 16" aria-hidden="true"><rect x="4" y="1" width="8" height="14" rx="1.5" fill="none" stroke="#e8433a" stroke-width="1.6"/><circle cx="8" cy="12.3" r="1" fill="#e8433a"/></svg>
        555 310-2746
      </li>
      <li class="contact__item">
        <svg class="contact__icon" viewBox="0 0 16 16" aria-hidden="true"><rect x="1" y="3" width="14" height="10" rx="1" fill="#e8433a"/><path d="M1.5 3.5L8 9l6.5-5.5" fill="none" stroke="#fff" stroke-width="1.3"/></svg>
        info@rowansfreshfloor.com
      </li>
      <li class="contact__item">
        <svg class="contact__icon" viewBox="0 0 16 16" aria-hidden="true"><circle cx="8" cy="8" r="7" fill="#e8433a"/><path d="M1 8h14M8 1c-3 3-3 11 0 14M8 1c3 3 3 11 0 14" fill="none" stroke="#fff" stroke-width="1"/></svg>
        www.rowansfreshfloor.com
      </li>
    </ul>
  </div>
</section>

</body>
</html>
```